IT’S NOT A CLEANING, IT’S YOUR LIFE! TOP TEN REASONS WHY THIS IS NOT JUST A “CLEANING”

We made a list for our patients to let them know why our hygiene appointments are different than other cleanings. Since this is a lot of information, we would like it easily readable within 4-5 feet but we do not want the post to be HUGE. Please see below:

IT’S NOT A CLEANING, IT’S YOUR LIFE!
TOP TEN REASONS WHY THIS IS NOT JUST A “CLEANING”

10. We make you look better. Healthy teeth and gums are more attractive. Recent studies
show that the smile is the first thing people notice and that people with better looking teeth
are more confident and successful.

9. We can relieve your headaches. During your hygiene visit we evaluate for serious bite
issues, many of which lead to muscle soreness, headaches, and migraines.

8. We check for oral cancer. Oral cancer kills 1 person per hour 24 hours a day. The death rate for oral cancer is higher than cancers we routinely hear about such as cervical, thyroid and skin cancer.

7. We make you smell better. During your hygiene visit we eliminate many of the germs that live under your gum tissue and cause bad breath.

6. We save you money. By utilizing the latest dental technology (digital x-rays, mouth
cameras, and magnification glasses) we can help with early detection of tooth and gum
problems and save you the cost of gum surgery, root canals, and implants.

5. We clean in places you cannot. We clean under the gum line and between teeth where
most of the germs hide and cause dental disease. 40% of the bacteria in your mouth lives in
between your teeth.

4. We prevent pain. We identify tooth decay that can lead to nerve involvement and pain,
root canal, and tooth loss.

3. We save your teeth. Most tooth loss is from periodontal/gum disease. At each visit we
evaluate the health of your gums and bone with our periodontal screening. Periodontal
disease, like high blood pressure, is symptomless until it is in advanced stages.

2. We protect your loved ones. Studies have proven that the bacteria that cause dental
disease can be transmitted from person to person. Think about that the next time you kiss
someone!

1. We prolong life. Researchers have linked the inflammation and infection found in the
mouth to heart attacks, strokes, and Alzheimer’s. By reducing infection in your mouth we can
greatly improve your overall health!

```html
<!DOCTYPE html>
<html lang="en">
<head>
<meta charset="utf-8">
<title>It's Not a Cleaning, It's Your Life!</title>
<link rel="stylesheet" href="https://fonts.googleapis.com/css2?family=Jost:wght@300;400;500&display=swap">
<style>
  :root {
    --paper: #ffffff;
    --wood-dark: #2a0d06;
    --wood-mid: #6b2410;
    --wood-warm: #9a3e18;
    --wood-glow: #b8561f;
    --shade: rgba(8, 3, 2, 0.72);
    --shade-soft: rgba(8, 3, 2, 0.55);
    --ink: #f4ece6;
  }
  * { margin: 0; padding: 0; box-sizing: border-box; }
  html, body { width: 776px; height: 1200px; overflow: hidden; background: var(--paper); }
  .poster {
    position: relative;
    width: 776px;
    height: 1200px;
    background: var(--paper);
    font-family: "Jost", "Century Gothic", sans-serif;
    color: var(--ink);
  }
  .wood {
    position: absolute;
    left: 14px; top: 14px; right: 14px; bottom: 12px;
    background:
      linear-gradient(180deg, rgba(0,0,0,0.25) 0%, rgba(0,0,0,0) 20%, rgba(0,0,0,0.1) 60%, rgba(0,0,0,0.3) 100%),
      linear-gradient(90deg, var(--wood-dark) 0%, var(--wood-mid) 25%, var(--wood-warm) 55%, var(--wood-glow) 80%, var(--wood-mid) 100%);
  }
  .header-band {
    position: absolute;
    left: 14px; right: 14px; top: 36px; height: 152px;
    background: var(--shade);
  }
  .title {
    position: absolute;
    left: 34px; top: 72px;
    font-weight: 500;
    font-size: 31px;
    letter-spacing: 0.5px;
    line-height: 1;
  }
  .subtitle {
    position: absolute;
    left: 34px; top: 127px;
    font-weight: 400;
    font-size: 24.5px;
    letter-spacing: 0.4px;
    line-height: 1;
  }
  .reasons { list-style: none; }
  .reason {
    position: absolute;
    left: 14px; right: 14px;
    padding: 6px 20px 8px 34px;
    background: var(--shade-soft);
    font-weight: 300;
    font-size: 16.6px;
    line-height: 22.6px;
    white-space: nowrap;
  }
  .reason-10 { top: 220px; }
  .reason-9  { top: 299px; }
  .reason-8  { top: 352px; }
  .reason-7  { top: 428px; }
  .reason-6  { top: 505px; }
  .reason-5  { top: 606px; }
  .reason-4  { top: 706px; }
  .reason-3  { top: 758px; }
  .reason-2  { top: 886px; }
  .reason-1  { top: 965px; }
</style>
</head>
<body>
<main class="poster">
  <div class="wood" role="img" aria-label="Warm reddish-brown wood plank background"></div>
  <div class="header-band"></div>
  <h1 class="title">IT’S NOT A CLEANING, IT’S YOUR LIFE!</h1>
  <h2 class="subtitle">TOP TEN REASONS WHY THIS IS NOT JUST A “CLEANING”</h2>

  <ol class="reasons">
    <li class="reason reason-10">10. We make you look better. Healthy teeth and gums are more attractive.<br>Recent studies show that the smile is the first thing people notice and that people with<br>better looking teeth are more confident and successful.</li>
    <li class="reason reason-9">9. We can relieve your headaches. During your hygiene visit we evaluate for serious<br>bite issues, many of which lead to muscle soreness, headaches, and migraines.</li>
    <li class="reason reason-8">8. We check for oral cancer. Oral cancer kills 1 person per hour 24 hours a day.<br>The death rate for oral cancer is higher than cancers we routinely hear about such as<br>cervical, thyroid and skin cancer.</li>
    <li class="reason reason-7">7. We make you smell better. During your hygiene visit we eliminate many of the<br>germs that live under your gum tissue and cause bad breath.</li>
    <li class="reason reason-6">6. We save you money. By utilizing the latest dental technology (digital x-rays, mouth<br>cameras, and magnification glasses) we can help with early detection of tooth and<br>gum problems and save you the cost of gum surgery, root canals, and implants.</li>
    <li class="reason reason-5">5. We clean in places you cannot. We clean under the gum line and between teeth<br>where most of the germs hide and cause dental disease. 40% of the bacteria in your<br>mouth lives in between your teeth.</li>
    <li class="reason reason-4">4. We prevent pain. We identify tooth decay that can lead to nerve involvement and<br>pain, root canal, and tooth loss.</li>
    <li class="reason reason-3">3. We save your teeth. Most tooth loss is from periodontal/gum disease. At each<br>visit we evaluate the health of your gums and bone with our periodontal screening.<br>Periodontal disease, like high blood pressure, is symptomless until it is in advanced<br>stages.</li>
    <li class="reason reason-2">2. We protect your loved ones. Studies have proven that the bacteria that cause<br>dental disease can be transmitted from person to person. Think about that the next<br>time you kiss someone</li>
    <li class="reason reason-1">1. We prolong life. Researchers have linked the inflammation and infection found in<br>the mouth to heart attacks, strokes, and Alzheimer’s. By reducing infection in your<br>mouth we can greatly improve your overall health!</li>
  </ol>
</main>
</body>
</html>
```